AMBER AND SLATE WEB

We need a home design in wordpress, we have now a web but we would like to improve it. Our current web is www.amberandslatevillas.example Our business is holliday rental of villas in Ibiza. Our guest must know that we are a reliable company, professional and with experience and good reviews. We want them to click in our reservation engine: https://bookings.amberandslatevillas.example/en/ and make reservation in our website. We would also like to say that all the properties that we have are just us who commercialize so we have best price available. Many people are going to see our villas in staylist.example and look to our website to make a reservation with us so we need to show them that they are at the right place and click at our link to our reservation engine. What make us special is that we are a local company, we are from Ibiza, Our guests are always received in person by the Amber and Slate Ibiza team. You will enjoy extensive tourist information when you check in and during the entire stay. You will be attended by ChatterLine and calls, always happy to help so that you have a happy and fun stay! Our guest stay is better than in hotel as they have more spece, private swiming pool, private garden, barbeque ... To rent a villa is the best way to stay in Ibiza. We also have a promotional video: https://vidshare.example/Qm7TzR2pLxA Let our philosophy be shown, we think that coming on holiday to Ibiza implies seeing the nature that we have in Ibiza, hence our name AMBER AND SLATE, like the pins that almost touch the sea in Ibiza, or the posidonea meadows where the intense green of the seaweed and the blue of the sea. We are aware of the environment, and we love Ibiza. For us, the client who visits Ibiza, should rent a car, go around the island, eat in a restaurant one day in front of the sea, is a night of partying to the discs, go shopping, visit the ancient heritage of Umanity, make some aquatic sport, enjoy the pool, those are for us Ibiza.

Target Market(s)

Europe, people from Holand, UK, Germany, France, Spain ...

Industry/Entity Type

Tourism

Colors

Designer to choose colors to be used in the design.

Requirements
Must have
• Pictures of Ibiza.
Nice to have
• Our name Amber and Slate Ibiza is beacuse in Ibiza there is forest that almost touch the watter of the Mediterranean sea, so you can see green of the forest and blue of the sea and the sky. And also beacause under the watter of the sea there is a plant called Posidonia that is also green please see the picture of posidonia.

```html
<!DOCTYPE html>
<html lang="en">
<head>
<meta charset="utf-8">
<title>Amber and Slate Villas Ibiza – Home</title>
<link rel="stylesheet" href="https://fonts.googleapis.com/css2?family=Cinzel:wght@400;500&family=Open+Sans:ital,wght@0,400;0,600;0,700;1,400&display=swap">
<style>
:root{
  --green:#8cb22a;
  --green-dark:#7a9d20;
  --blue:#2a8fd2;
  --blue-deep:#1f6fa8;
  --ink:#333;
  --muted:#555;
  --white:#fff;
  --black:#0d0d0d;
}
*{box-sizing:border-box;margin:0;padding:0}
html,body{width:1200px;height:4013px;overflow:hidden}
body{position:relative;font-family:'Open Sans',sans-serif;color:var(--ink);background:var(--white)}
.abs{position:absolute}
.serif{font-family:'Cinzel',serif;font-weight:400}

/* hero */
.hero{left:0;top:0;width:1200px;height:665px;background:
  linear-gradient(180deg,#1f4b86 0%,#3f78b6 20%,#2f7ea8 38%,#19a7c8 55%,#2ab6c5 68%,#3d6d3a 80%,#d6c7a3 100%)}
.logo{left:112px;top:64px;color:var(--white);font-family:'Cinzel',serif;font-size:34px;letter-spacing:1px;white-space:nowrap}
.topbar-phone{left:545px;top:40px;color:var(--white);font-size:17px;display:flex;align-items:center;gap:8px}
.pill{height:45px;border:2px solid var(--white);border-radius:23px;color:var(--white);font-size:14px;font-weight:700;display:flex;align-items:center;justify-content:center}
.lang{left:1039px;top:41px;color:var(--white);font-size:14px;font-weight:600}
.nav{top:99px;color:var(--white);font-size:15px;font-weight:600}
.nav.active{color:#a9d036}
.hero-title{left:0;width:1200px;top:222px;text-align:center;color:var(--white);font-size:58px}
.booking{left:145px;top:329px;width:911px;height:106px;background:rgba(20,35,50,.55);border-radius:4px}
.field{top:355px;height:53px;background:var(--white);font-size:14px;color:#555;display:flex;align-items:center;padding-left:24px;gap:8px;border-right:1px solid #ddd}
.btn-green{background:var(--green);color:var(--white);font-weight:700;border-radius:28px;display:flex;align-items:center;justify-content:center}
.dot{top:583px;width:14px;height:14px;border-radius:50%;border:2px solid var(--white)}

/* welcome */
.welcome-title{left:112px;top:750px;font-size:46px;line-height:59px;color:var(--ink)}
.body-copy{font-size:14px;line-height:28px;color:var(--muted)}
.outline-btn{left:112px;top:1130px;width:139px;height:50px;border:2px solid var(--green);border-radius:25px;color:var(--green);font-weight:700;font-size:15px;display:flex;align-items:center;justify-content:center}
.photo{display:block}
.play{width:60px;height:60px;border-radius:50%;background:#111;display:flex;align-items:center;justify-content:center}

/* services */
.services{left:0;top:1271px;width:1200px;height:819px;background:linear-gradient(180deg,#1f86cc 0%,#2a95d4 45%,#3ea3d6 100%)}
.section-title{left:0;width:1200px;text-align:center;font-size:44px}
.svc-circle{width:171px;height:171px;border-radius:50%;background:var(--white);box-shadow:6px 8px 0 #1d5f8f;display:flex;align-items:center;justify-content:center}
.svc-label{width:280px;text-align:center;color:var(--white);font-size:22px;line-height:30px}

/* blog */
.card-img{height:201px;border:4px solid var(--white);box-shadow:0 0 0 1px #ddd}
.card-title{font-size:19px;line-height:30px;color:#222;width:310px}
.meta{font-size:14px;color:#444;display:flex;align-items:center;gap:6px}

/* experience */
.experience{left:0;top:2727px;width:1200px;height:735px;background:linear-gradient(180deg,#9cc53a 0%,#86b52c 50%,#6f9f24 100%)}
.exp-copy{left:210px;width:780px;top:2900px;text-align:center;color:var(--white);font-style:italic;font-size:15px;line-height:29px}
.arrow-btn{width:54px;height:54px;border-radius:50%;border:2px solid var(--white);display:flex;align-items:center;justify-content:center}

/* footer */
.footer{left:0;top:3462px;width:1200px;height:551px;background:var(--black)}
.foot-h{color:var(--white);font-size:21px;font-weight:600;letter-spacing:.3px}
.input{background:var(--white);height:31px;font-size:12px;color:#666;padding:9px 14px}
.info-icon{width:34px;height:34px;border-radius:50%;border:1.5px solid var(--green);display:flex;align-items:center;justify-content:center}
.info-text{color:#ddd;font-size:14px;line-height:24px}
.social{width:42px;height:42px;border-radius:50%;border:1.5px solid var(--green)}
</style>
</head>
<body>

<!-- HERO -->
<div class="abs hero" role="img" aria-label="Photo of an Ibiza cove: pine-covered cliffs, turquoise water and a sandy beach with boats"></div>
<div class="abs logo">AMBER AND SLATE</div>
<div class="abs topbar-phone">
  <svg width="16" height="16" viewBox="0 0 24 24"><path fill="#8cc63f" d="M6.6 10.8c1.4 2.8 3.8 5.1 6.6 6.6l2.2-2.2c.3-.3.7-.4 1-.2 1.1.4 2.3.6 3.6.6.6 0 1 .4 1 1V20c0 .6-.4 1-1 1C10.6 21 3 13.4 3 4c0-.6.4-1 1-1h3.5c.6 0 1 .4 1 1 0 1.3.2 2.5.6 3.6.1.3 0 .7-.2 1z"/></svg>
  +34600111222
</div>
<div class="abs pill" style="left:713px;top:28px;width:161px">ALL PROPERTIES</div>
<div class="abs pill" style="left:885px;top:28px;width:134px">BOOK NOW!</div>
<div class="abs lang">ENG <svg width="10" height="8" viewBox="0 0 10 8"><path d="M1 2l4 4 4-4" stroke="#fff" stroke-width="1.5" fill="none"/></svg></div>
<div class="abs nav active" style="left:615px">HOME</div>
<div class="abs nav" style="left:698px">EXPERIENCE</div>
<div class="abs nav" style="left:826px">ABOUT US</div>
<div class="abs nav" style="left:941px">CONTACT US</div>
<svg class="abs" style="left:1076px;top:102px" width="16" height="16" viewBox="0 0 16 16"><circle cx="6.5" cy="6.5" r="4.5" stroke="#fff" stroke-width="2" fill="none"/><path d="M10 10l4 4" stroke="#fff" stroke-width="2.4"/></svg>

<h1 class="abs hero-title serif">The Best Way to Stay in Ibiza!</h1>
<div class="abs booking"></div>
<div class="abs field" style="left:170px;width:246px">Best available rate</div>
<div class="abs field" style="left:416px;width:265px">
  <svg width="13" height="13" viewBox="0 0 14 14"><rect x="1" y="2.5" width="12" height="10.5" fill="none" stroke="#777" stroke-width="1.4"/><path d="M1 5.5h12M4 1v3M10 1v3" stroke="#777" stroke-width="1.4"/></svg>
  Chek - in - Check - out
</div>
<div class="abs field" style="left:681px;width:185px;border-right:none">
  <svg width="12" height="13" viewBox="0 0 12 13"><circle cx="6" cy="3.5" r="3" fill="#777"/><path d="M0 13c0-4 2.5-6 6-6s6 2 6 6z" fill="#777"/></svg>
  2 adults 0 Kids
</div>
<div class="abs btn-green" style="left:883px;top:355px;width:147px;height:55px;font-size:16px">BOOK NOW!</div>
<div class="abs dot" style="left:562px;background:var(--white)"></div>
<div class="abs dot" style="left:582px"></div>
<div class="abs dot" style="left:602px"></div>
<div class="abs dot" style="left:622px"></div>

<!-- WELCOME -->
<h2 class="abs welcome-title serif">Welcome to Amber<br>&amp; Slate Villas Ibiza</h2>
<p class="abs body-copy" style="left:112px;top:891px;width:500px">Amber and Slate Villas Ibiza is a company specialized in offering its clients accommodation in Villas on the countryside of Ibiza. Our guests enjoy the rural Ibiza, tranquility, relax, private pool, close to dream beaches and coves, the best restaurants, an unforgettable holiday for family or friends.</p>
<p class="abs body-copy" style="left:112px;top:1033px;width:500px">Every day can be a different experience, beach, restaurant, flea market, disco, hiking, kayaking, horseback riding, shopping, history, boat ride!</p>
<div class="abs outline-btn">READ MORE</div>
<div class="abs photo" style="left:647px;top:762px;width:441px;height:308px;background:linear-gradient(180deg,#7aa4c6 0%,#3f6f94 45%,#b8643a 60%,#c9814e 100%);box-shadow:0 2px 8px rgba(0,0,0,.2)" role="img" aria-label="Video still: two people standing on red coastal cliffs above the sea"></div>
<div class="abs play" style="left:838px;top:886px"><svg width="22" height="24" viewBox="0 0 22 24"><path d="M3 2l17 10-17 10z" fill="#fff"/></svg></div>

<!-- SERVICES -->
<div class="abs services" role="img" aria-label="Underwater photo of a posidonia seagrass meadow in blue water"></div>
<h2 class="abs section-title serif" style="top:1350px;color:var(--white)">Services</h2>

<div class="abs svc-circle" style="left:116px;top:1447px">
  <svg width="120" height="60" viewBox="0 0 120 60"><path d="M10 40v-12l16-4 14-14h40l18 14 12 3v13z" fill="#8cb22a"/><path d="M44 14h16v12H30zM64 14h14l14 12H64z" fill="#fff"/><circle cx="32" cy="42" r="10" fill="#8cb22a" stroke="#fff" stroke-width="3"/><circle cx="90" cy="42" r="10" fill="#8cb22a" stroke="#fff" stroke-width="3"/></svg>
</div>
<div class="abs svc-circle" style="left:382px;top:1447px">
  <svg width="100" height="100" viewBox="0 0 100 100"><path d="M40 30c-2 20-4 35-8 52h8c3-17 5-32 4-52z" fill="#8cb22a"/><path d="M42 30c-14-12-28-6-32 4 10-6 20-6 32-4zM42 30c14-14 30-8 34 2-10-6-22-6-34-2zM42 30c-4-12-14-20-24-18 10 2 18 10 24 18zM42 30c6-10 16-18 28-16-12 2-20 8-28 16z" fill="#8cb22a"/><path d="M64 44c-1 14-3 24-6 38h6c2-14 3-24 2-38zM65 44c10-8 20-4 24 2-8-4-16-4-24-2zM65 44c-10-9-20-5-24 1 8-4 16-3 24-1z" fill="#8cb22a"/><path d="M14 84c12-6 60-6 72 0M18 92c6-3 10-3 16 0s10 3 16 0 10-3 16 0 10 3 16 0" stroke="#8cb22a" stroke-width="4" fill="none"/></svg>
</div>
<div class="abs svc-circle" style="left:647px;top:1447px">
  <svg width="90" height="90" viewBox="0 0 90 90"><path d="M30 10v22M24 10v10c0 4 12 4 12 0V10M60 10c-6 0-8 10-8 20h8v10" stroke="#8cb22a" stroke-width="4" fill="none"/><rect x="14" y="44" width="62" height="7" fill="#8cb22a"/><path d="M22 51v32M68 51v32M8 56v27M82 56v27M8 70h12M70 70h12" stroke="#8cb22a" stroke-width="5"/></svg>
</div>
<div class="abs svc-circle" style="left:913px;top:1447px">
  <svg width="90" height="90" viewBox="0 0 90 90"><path d="M45 6v14" stroke="#8cb22a" stroke-width="3"/><circle cx="45" cy="50" r="28" fill="none" stroke="#8cb22a" stroke-width="4"/><path d="M17 50h56M45 22v56M22 36h46M22 64h46M31 26v48M59 26v48" stroke="#8cb22a" stroke-width="3"/><rect x="31" y="36" width="14" height="14" fill="#8cb22a"/><rect x="45" y="50" width="14" height="14" fill="#8cb22a"/><path d="M12 18l2 5 5 2-5 2-2 5-2-5-5-2 5-2zM78 60l2 4 4 2-4 2-2 4-2-4-4-2 4-2z" fill="#8cb22a"/></svg>
</div>
<div class="abs svc-label" style="left:61px;top:1647px">Rent a car</div>
<div class="abs svc-label" style="left:327px;top:1647px">Go around<br>the island</div>
<div class="abs svc-label" style="left:592px;top:1647px">Eat in a restaurant one<br>day in front of the sea</div>
<div class="abs svc-label" style="left:859px;top:1647px">Night Party</div>

<div class="abs svc-circle" style="left:116px;top:1747px">
  <svg width="90" height="100" viewBox="0 0 90 100"><path d="M30 30c0-22 30-22 30 0" stroke="#8cb22a" stroke-width="4" fill="none"/><path d="M12 30h66l6 64H6z" fill="none" stroke="#8cb22a" stroke-width="5"/><path d="M45 78c-16-10-18-22-10-26 4-2 8 0 10 4 2-4 6-6 10-4 8 4 6 16-10 26z" fill="#8cb22a"/></svg>
</div>
<div class="abs svc-circle" style="left:382px;top:1747px">
  <svg width="70" height="110" viewBox="0 0 70 110"><path d="M35 4v8M20 20l15-8 15 8z" stroke="#8cb22a" stroke-width="4" fill="#8cb22a"/><rect x="14" y="22" width="42" height="8" fill="#8cb22a"/><path d="M16 30h38v66H16z" fill="none" stroke="#8cb22a" stroke-width="5"/><path d="M26 52h18v30H26z" fill="none" stroke="#8cb22a" stroke-width="5"/><rect x="8" y="96" width="54" height="8" fill="#8cb22a"/></svg>
</div>
<div class="abs svc-circle" style="left:647px;top:1747px">
  <svg width="110" height="80" viewBox="0 0 110 80"><path d="M10 56c20 6 60 8 90-6l-6 14c-28 10-62 8-84 0z" fill="#8cb22a"/><path d="M30 52l14-14h26l10 12z" fill="#8cb22a"/><circle cx="58" cy="18" r="7" fill="#8cb22a"/><path d="M4 74c10-4 20-4 30 0s20 4 30 0 20-4 30 0" stroke="#8cb22a" stroke-width="4" fill="none"/></svg>
</div>
<div class="abs svc-circle" style="left:913px;top:1747px">
  <svg width="110" height="90" viewBox="0 0 110 90"><ellipse cx="50" cy="58" rx="40" ry="16" fill="none" stroke="#8cb22a" stroke-width="6"/><path d="M64 70V20c0-8 12-8 12 0M80 60V16c0-8 12-8 12 0M64 36h16M64 50h16" stroke="#8cb22a" stroke-width="5" fill="none"/><path d="M26 58c6-4 12-4 18 0s12 4 18 0" stroke="#8cb22a" stroke-width="4" fill="none"/></svg>
</div>
<div class="abs svc-label" style="left:61px;top:1948px">Go shopping</div>
<div class="abs svc-label" style="left:327px;top:1948px">Visit the ancient<br>heritage of humanity</div>
<div class="abs svc-label" style="left:592px;top:1948px">Aquatic sport</div>
<div class="abs svc-label" style="left:859px;top:1948px">Enjoy the pool</div>

<!-- BLOG -->
<h2 class="abs section-title serif" style="top:2185px;color:var(--ink)">Latest Blog</h2>

<div class="abs card-img" style="left:111px;top:2287px;width:308px;background:linear-gradient(180deg,#4f8fd6 0%,#8fbde8 35%,#2a78b8 55%,#17a2b0 100%)" role="img" aria-label="Photo of a rocky islet rising from turquoise sea with boats"></div>
<div class="abs card-img" style="left:446px;top:2287px;width:308px;background:linear-gradient(135deg,#5a8fb0 0%,#d6a27a 45%,#b5405a 75%,#3a5e9a 100%)" role="img" aria-label="Photo of friends celebrating at a beach party at dusk"></div>
<div class="abs card-img" style="left:779px;top:2287px;width:309px;background:linear-gradient(180deg,#3a86d6 0%,#9cc8ee 30%,#1f8fb0 55%,#4f8a3a 85%,#2f6a2a 100%)" role="img" aria-label="Photo of a bay with a sandy beach, clear water and pine-covered hills"></div>

<div class="abs card-title" style="left:109px;top:2520px">Nemo enim ipsam voluptaquia vo luptas sit aspernatur aut</div>
<div class="abs card-title" style="left:445px;top:2520px">Nemo enim ipsam voluptaquia vo luptas sit aspernatur aut</div>
<div class="abs card-title" style="left:779px;top:2520px">Nemo enim ipsam voluptaquia vo luptas sit aspernatur aut</div>

<div class="abs meta" style="left:110px;top:2597px"><svg width="12" height="12" viewBox="0 0 14 14"><rect x="1" y="2.5" width="12" height="10.5" fill="none" stroke="#8cb22a" stroke-width="1.6"/><path d="M1 5.5h12" stroke="#8cb22a" stroke-width="1.6"/></svg>12/19/2019&nbsp;&nbsp;|&nbsp;<svg width="11" height="12" viewBox="0 0 12 13"><circle cx="6" cy="3.5" r="3" fill="#2a8fd2"/><path d="M0 13c0-4 2.5-6 6-6s6 2 6 6z" fill="#2a8fd2"/></svg>Mara Vell</div>
<div class="abs meta" style="left:446px;top:2597px"><svg width="12" height="12" viewBox="0 0 14 14"><rect x="1" y="2.5" width="12" height="10.5" fill="none" stroke="#8cb22a" stroke-width="1.6"/><path d="M1 5.5h12" stroke="#8cb22a" stroke-width="1.6"/></svg>12/19/2019&nbsp;&nbsp;|&nbsp;<svg width="11" height="12" viewBox="0 0 12 13"><circle cx="6" cy="3.5" r="3" fill="#2a8fd2"/><path d="M0 13c0-4 2.5-6 6-6s6 2 6 6z" fill="#2a8fd2"/></svg>Mara Vell</div>
<div class="abs meta" style="left:780px;top:2597px"><svg width="12" height="12" viewBox="0 0 14 14"><rect x="1" y="2.5" width="12" height="10.5" fill="none" stroke="#8cb22a" stroke-width="1.6"/><path d="M1 5.5h12" stroke="#8cb22a" stroke-width="1.6"/></svg>12/19/2019&nbsp;&nbsp;|&nbsp;<svg width="11" height="12" viewBox="0 0 12 13"><circle cx="6" cy="3.5" r="3" fill="#2a8fd2"/><path d="M0 13c0-4 2.5-6 6-6s6 2 6 6z" fill="#2a8fd2"/></svg>Mara Vell</div>

<!-- EXPERIENCE -->
<div class="abs experience" role="img" aria-label="Close-up photo of green grass blades in sunlight"></div>
<h2 class="abs section-title serif" style="top:2808px;color:var(--white)">Experience</h2>
<p class="abs exp-copy">Nemo enim ipsam voluptatem quia voluptas sit aspernatur aut odit aut fugit, sed quia consequuntur magni dolores eos qui ratione voluptatem sequi nesciunt. Neque porro quisquam est, qui dolorem ipsum quia dolor sit amet, consectetur, adipisci velit, sed quia non numquam eius modi tempora incidun.</p>
<div class="abs" style="left:0;width:1200px;top:3008px;text-align:center;color:var(--white);font-size:21px;font-weight:600">Amber and Slate ibiza entrevista aleman 1</div>
<div class="abs" style="left:379px;top:3096px;width:442px;height:265px;background:linear-gradient(135deg,#e6e2dc 0%,#c9a27c 40%,#8a6a4e 70%,#5c7fa8 100%)" role="img" aria-label="Video still: interview with a guest in front of a stone wall"></div>
<div class="abs play" style="left:570px;top:3198px;background:rgba(0,0,0,.35);border:2px solid #fff"><svg width="22" height="24" viewBox="0 0 22 24"><path d="M4 2l16 10-16 10z" fill="#fff"/></svg></div>
<div class="abs arrow-btn" style="left:245px;top:3201px"><svg width="14" height="22" viewBox="0 0 14 22"><path d="M11 2L3 11l8 9" stroke="#fff" stroke-width="2.4" fill="none"/></svg></div>
<div class="abs arrow-btn" style="left:895px;top:3201px"><svg width="14" height="22" viewBox="0 0 14 22"><path d="M3 2l8 9-8 9" stroke="#fff" stroke-width="2.4" fill="none"/></svg></div>

<!-- FOOTER -->
<div class="abs footer"></div>
<div class="abs foot-h" style="left:111px;top:3556px">CONTACT US</div>
<div class="abs input" style="left:112px;top:3627px;width:310px">First Name</div>
<div class="abs input" style="left:432px;top:3627px;width:310px">Last Name</div>
<div class="abs input" style="left:112px;top:3672px;width:310px">Email</div>
<div class="abs input" style="left:432px;top:3672px;width:310px">Phone Number</div>
<div class="abs input" style="left:112px;top:3720px;width:630px;height:81px;padding-top:14px">Comments</div>
<div class="abs btn-green" style="left:112px;top:3820px;width:115px;height:44px;font-size:15px">SUBMIT</div>

<div class="abs foot-h" style="left:790px;top:3554px">CONTACT INFORMATION</div>
<div class="abs info-icon" style="left:790px;top:3624px"><svg width="12" height="16" viewBox="0 0 12 16"><path d="M6 0C2.7 0 0 2.6 0 5.8 0 10 6 16 6 16s6-6 6-10.2C12 2.6 9.3 0 6 0z" fill="#8cb22a"/><circle cx="6" cy="6" r="2.2" fill="#0d0d0d"/></svg></div>
<div class="abs info-text" style="left:848px;top:3618px">42 Harbour Lane<br>Suite 7 Portmar, IB 07800</div>
<div class="abs info-icon" style="left:790px;top:3694px"><svg width="14" height="14" viewBox="0 0 24 24"><path fill="#8cb22a" d="M6.6 10.8c1.4 2.8 3.8 5.1 6.6 6.6l2.2-2.2c.3-.3.7-.4 1-.2 1.1.4 2.3.6 3.6.6.6 0 1 .4 1 1V20c0 .6-.4 1-1 1C10.6 21 3 13.4 3 4c0-.6.4-1 1-1h3.5c.6 0 1 .4 1 1 0 1.3.2 2.5.6 3.6.1.3 0 .7-.2 1z"/></svg></div>
<div class="abs info-text" style="left:848px;top:3699px">+34600111222</div>
<div class="abs info-icon" style="left:790px;top:3752px"><svg width="14" height="14" viewBox="0 0 14 14"><rect x="1" y="4" width="12" height="9" fill="#8cb22a"/><rect x="4" y="1" width="6" height="4" fill="none" stroke="#8cb22a" stroke-width="1.4"/></svg></div>
<div class="abs info-text" style="left:848px;top:3757px">+34 600 333 444</div>
<div class="abs info-icon" style="left:790px;top:3810px"><svg width="14" height="12" viewBox="0 0 14 12"><rect x="0" y="1" width="14" height="10" fill="#8cb22a"/><path d="M0 1l7 6 7-6" stroke="#0d0d0d" stroke-width="1.4" fill="none"/></svg></div>
<div class="abs info-text" style="left:848px;top:3815px">info@amberandslatevillas.example</div>

<div class="abs" style="left:98px;top:3901px;width:1003px;height:1px;background:#333"></div>
<div class="abs" style="left:111px;top:3944px;color:#ddd;font-size:14px">Copyright © 2019, Amber and Slate Villas Ibiza. All right reserved.</div>
<div class="abs social" style="left:845px;top:3933px"></div>
<div class="abs social" style="left:895px;top:3933px"></div>
<div class="abs social" style="left:945px;top:3933px"></div>
<div class="abs social" style="left:995px;top:3933px"></div>
<div class="abs social" style="left:1046px;top:3933px"></div>

</body>
</html>
```